Design and Renovation Company Luxury Business Card

I want to create a luxury business card for a Interiors & Remodel Studio . We will use our current logo. The company name is 528BUILDA. We do not want anything standard. We need a very unique concept.
Please see uploaded inspiration. I really like the textured paper option. I would like the card to be thick with debossing, and/or embossing options. The logo has orange in it but I would like to see the card with and without the orange. I think the orange may make the company feel less high-end. The goal is to elevate the logo not match its vibe per se of the logo. We want something very unique, not standard at all!
I would like a space for :
Logo,
Name,
Position,
Email,
Office number,
Website Address,
Business Address,
Thank you!
Have fun!
Target Market(s)
Home owners Age 35 +
Industry/Entity Type
Design and Renovation
Contact Information for Business Card
Logo, Name, Position, Email, Office number, Website Address, Business Address,.
Colors
Designer to choose colors to be used in the design.
Requirements
Must have
- A luxury designer feel. Must be black or dark grey but open to other luxury ideas.
Nice to have
- Gold, silver, black embossing or debossing. Textured paper design.
Should not have
- A cheap look and feel.

```html
<!DOCTYPE html>
<html lang="en">
<head>
<meta charset="utf-8">
<title>528BUILDA Business Card</title>
<link rel="stylesheet" href="https://fonts.googleapis.com/css2?family=Montserrat:wght@400;500;700&display=swap">
<style>
  :root {
    --page-bg: #d9d4cc;
    --card-white: #ffffff;
    --card-black: #141414;
    --ink: #111111;
    --ink-soft: #222222;
    --accent: #f39322;
    --rule: #1a1a1a;
    --photo-warm: #fdf3ea;
    --photo-grey: #e8e8e8;
    --back-text: #2a2a2a;
  }
  * { margin: 0; padding: 0; box-sizing: border-box; }
  html, body { width: 900px; height: 1200px; overflow: hidden; }
  body { background: var(--page-bg); position: relative; font-family: "Montserrat", sans-serif; color: var(--ink); }

  .card { position: absolute; left: 80px; width: 742px; height: 441px; border-radius: 22px; overflow: hidden; }
  .card-front { top: 131px; background: var(--card-white); }
  .card-back { top: 638px; background: var(--card-black); }

  .brand-name { font-family: "Montserrat", sans-serif; font-weight: 500; font-size: 54px; line-height: 1; letter-spacing: 2px; color: var(--ink); white-space: nowrap; }
  .brand-tagline { font-family: "Montserrat", sans-serif; font-weight: 400; font-size: 15px; letter-spacing: 2.4px; color: var(--ink-soft); margin-top: 10px; white-space: nowrap; }

  .card-front .brand { position: absolute; left: 35px; top: 62px; }

  .project-photo { position: absolute; width: 127px; height: 126px; }
  .photo-top { left: 568px; top: 31px; background: var(--photo-warm); }
  .photo-left { left: 419px; top: 179px; background: var(--photo-grey); }
  .photo-right { left: 568px; top: 179px; background: var(--photo-grey); }

  .holder { position: absolute; left: 34px; top: 258px; }
  .holder-name { font-weight: 700; font-size: 26px; line-height: 1; }
  .holder-role { font-size: 16px; margin-top: 8px; color: var(--ink-soft); }

  .divider { position: absolute; left: 33px; top: 312px; width: 663px; height: 2px; background: var(--rule); }

  .contacts { position: absolute; left: 36px; top: 331px; list-style: none; }
  .contacts li { display: flex; align-items: center; font-size: 16px; height: 28px; }
  .contacts svg { width: 14px; height: 14px; margin-right: 10px; fill: var(--accent); }

  .address { position: absolute; right: 47px; top: 369px; text-align: right; font-size: 16px; line-height: 21px; }

  .footer-band { position: absolute; left: 0; bottom: 0; width: 742px; height: 19px; }

  .card-back .brand { position: absolute; left: 0; right: 0; top: 180px; text-align: center; }
  .card-back .brand-name { color: var(--back-text); font-size: 60px; }
  .card-back .brand-tagline { color: var(--back-text); font-size: 16px; }
</style>
</head>
<body>
  <section class="card card-front" aria-label="Business card front">
    <div class="brand">
      <div class="brand-name">528BUILDA</div>
      <div class="brand-tagline">Interiors &amp; Remodel Studio</div>
    </div>

    <div class="project-photo photo-top" role="img" aria-label="Project photo placeholder"></div>
    <div class="project-photo photo-left" role="img" aria-label="Project photo placeholder"></div>
    <div class="project-photo photo-right" role="img" aria-label="Project photo placeholder"></div>

    <div class="holder">
      <div class="holder-name">Daniel Hart</div>
      <div class="holder-role">Managing Director</div>
    </div>

    <div class="divider"></div>

    <ul class="contacts">
      <li><svg viewBox="0 0 24 24"><path d="M6.6 10.8a15.1 15.1 0 0 0 6.6 6.6l2.2-2.2a1 1 0 0 1 1-.25 11.4 11.4 0 0 0 3.6.57 1 1 0 0 1 1 1V20a1 1 0 0 1-1 1A17 17 0 0 1 3 4a1 1 0 0 1 1-1h3.5a1 1 0 0 1 1 1c0 1.25.2 2.45.57 3.57a1 1 0 0 1-.25 1z"/></svg>555-318-0427</li>
      <li><svg viewBox="0 0 24 24"><path d="M2 5h20v14H2z"/><path d="M2 5l10 7 10-7" fill="none" stroke="#fff" stroke-width="2"/></svg>info@yourstudioname.com</li>
      <li><svg viewBox="0 0 24 24"><circle cx="12" cy="12" r="10"/><path d="M2 12h20M12 2c3 3 3 17 0 20M12 2c-3 3-3 17 0 20" fill="none" stroke="#fff" stroke-width="1.5"/></svg>www.yourstudioname.com</li>
    </ul>

    <div class="address">415 Elm Grove Ave, #112<br>Fairview, OH 430511</div>

    <svg class="footer-band" viewBox="0 0 742 19" preserveAspectRatio="none" aria-hidden="true">
      <polygon points="0,0 488,0 474,19 0,19" fill="var(--ink)"/>
      <polygon points="494,0 742,0 742,19 480,19" fill="var(--accent)"/>
    </svg>
  </section>

  <section class="card card-back" aria-label="Business card back">
    <div class="brand">
      <div class="brand-name">528BUILDA</div>
      <div class="brand-tagline">Interiors &amp; Remodel Studio</div>
    </div>
  </section>
</body>
</html>
```